IT Company that provides secure IT solutions and services to our customers

We need business cards and a logo for a new IT Solutions company just created based in Kuala Lumpur, Malaysia. But will also be serving other countries in the region. We provide secure data, voice solutions on mobile platforms. Our first offering is encrypted voice and data solutions for IOS, Android, Windows and BlackBerry devices.

Target Market(s)

large organizations Govt, Police, Defence, Anti-corruption, Legal, highly regulated industries such as Health-care, Financial, Banking, Insurance,

Industry/Entity Type

Information Technology

Contact Information for Business Card

VelmoraNet (Logo - colour is ORVEX blue)Roshan Adeel Managing Director Kryption IT Sdn. Bhd.5th Floor, Block D, Wisma PLB,No.14 Jalan Seri Melor,50470, Kuala LumpurMalaysia

Font styles to use
Sans Serif

Colors
3176b5
ec1f27
fbed22

Requirements
Must have
• VelmoraNet all in Blue like ORVEX blue. A logo design perhaps a play of VN, K with a dangling T (colour can be any)
Nice to have
• I want a clean crisp card, not too busy, easy to read.

```html
<!DOCTYPE html>
<html lang="en">
<head>
<meta charset="utf-8">
<title>VelmoraNet Business Cards</title>
<link rel="stylesheet" href="https://fonts.googleapis.com/css2?family=Arimo:wght@400;700&display=swap">
<style>
  :root {
    --backdrop: #c9c9d0;
    --card: #ecebea;
    --brand-blue: #3a93c6;
    --brand-yellow: #e1d94a;
    --ink: #3f3f42;
    --ink-soft: #55565a;
  }
  * { margin: 0; padding: 0; box-sizing: border-box; }
  html, body {
    width: 1200px;
    height: 1000px;
    overflow: hidden;
    background: var(--backdrop);
    font-family: "Arimo", Arial, sans-serif;
  }
  .canvas {
    position: relative;
    width: 1200px;
    height: 1000px;
  }
  .card {
    position: absolute;
    width: 760px;
    height: 434px;
    background: var(--card);
    box-shadow: 0 2px 6px rgba(0,0,0,0.12);
  }
  .card--back { left: 60px; top: 50px; }
  .card--front { left: 380px; top: 516px; }

  .brand {
    position: absolute;
    display: flex;
    align-items: center;
    gap: 18px;
  }
  .brand__dot {
    width: 58px;
    height: 58px;
    border-radius: 50%;
    background: var(--brand-yellow);
  }
  .brand__name {
    font-weight: 700;
    font-size: 66px;
    letter-spacing: -1px;
    color: var(--brand-blue);
    line-height: 1;
  }
  .card--back .brand { left: 110px; top: 58px; }
  .card--front .brand { left: 110px; top: 92px; }

  .address {
    position: absolute;
    left: 140px;
    top: 178px;
    font-size: 21px;
    line-height: 1.3;
    color: var(--ink);
    font-style: normal;
  }

  .person {
    position: absolute;
    left: 300px;
    top: 196px;
    color: var(--ink);
  }
  .person__name {
    font-weight: 700;
    font-size: 25px;
    letter-spacing: 2px;
    text-transform: uppercase;
  }
  .person__title {
    margin-top: 6px;
    font-size: 23px;
    letter-spacing: 1px;
    color: var(--ink-soft);
  }
</style>
</head>
<body>
  <main class="canvas">
    <section class="card card--back" aria-label="Business card back">
      <div class="brand">
        <span class="brand__dot"></span>
        <span class="brand__name">VelmoraNet</span>
      </div>
      <address class="address">
        Velmora Net Sdn. Bhd<br>
        5th Floor, Block D<br>
        Wisma PLB No. 14<br>
        Jalan Seri Melor<br>
        50470 Kuala Lumpur<br>
        Malaysia
      </address>
    </section>

    <section class="card card--front" aria-label="Business card front">
      <div class="brand">
        <span class="brand__dot"></span>
        <span class="brand__name">VelmoraNet</span>
      </div>
      <div class="person">
        <p class="person__name">Roshan Adeel</p>
        <p class="person__title">Managing Director</p>
      </div>
    </section>
  </main>
</body>
</html>
```